Design a Brazilian children's Bible calendar for 2017

We need someone to design a children's calendar for 2017 with an animal theme.
The format is 21cm x 15cm and we need the front cover and one page with two months as can be seen in the attached files.
Target Market(s)
Brazilian children
Font styles to use
Sans Serif
Requirements
Must have
- Modern, clean design

```html
<!DOCTYPE html>
<html lang="pt-BR">
<head>
<meta charset="utf-8">
<title>Calendário 2017 — Setembro e Outubro</title>
<link href="https://fonts.googleapis.com/css2?family=Raleway:wght@500;600;700&family=Quicksand:wght@400;500&family=Nunito:wght@900&display=swap" rel="stylesheet">
<style>
  :root {
    --page-bg: #b28fae;
    --ink-purple: #6a0f86;
    --white: #ffffff;
    --photo-top: #8d9a86;
    --photo-mid: #d6b64a;
    --photo-low: #e8c23a;
    --meadow-green: rgba(70, 120, 60, 0.28);
  }
  * { margin: 0; padding: 0; box-sizing: border-box; }
  html, body { width: 856px; height: 1200px; overflow: hidden; background: var(--page-bg); }
  .calendar-page { position: relative; width: 856px; height: 1200px; background: var(--page-bg); font-family: "Quicksand", sans-serif; }

  .hero-photo {
    position: absolute; left: 0; top: 0; width: 856px; height: 600px;
    background:
      radial-gradient(ellipse 170px 240px at 250px 360px, rgba(245,240,230,0.85), rgba(245,240,230,0) 100%),
      linear-gradient(180deg, var(--photo-top) 0%, #b4a770 22%, var(--photo-mid) 45%, var(--photo-low) 75%, #b99a2e 100%);
  }
  .hero-verse {
    position: absolute; left: 419px; top: 230px; width: 400px; text-align: center;
    font-family: "Raleway", sans-serif; color: var(--ink-purple);
  }
  .hero-verse__text { font-size: 31px; font-weight: 600; line-height: 36px; }
  .hero-verse__ref { margin-top: 10px; font-size: 17px; font-weight: 700; letter-spacing: 0.3px; }

  .meadow-illustration {
    position: absolute; left: 48px; top: 629px; width: 740px; height: 170px;
    background: linear-gradient(180deg, rgba(255,255,255,0) 0%, rgba(255,255,255,0) 55%, var(--meadow-green) 100%);
    border-radius: 6px;
  }
  .year-title {
    position: absolute; left: 0; width: 856px; top: 738px; text-align: center;
    font-family: "Nunito", sans-serif; font-weight: 900; font-size: 58px; line-height: 60px;
    color: var(--ink-purple); letter-spacing: -1px; padding-right: 20px;
  }

  .month { position: absolute; top: 806px; width: 331px; }
  .month--september { left: 65px; }
  .month--october { left: 460px; }
  .month__name {
    text-align: center; color: var(--white); font-size: 50px; font-weight: 400; line-height: 56px;
  }
  .month__weekdays, .month__days {
    display: grid; grid-template-columns: repeat(7, 47.3px);
  }
  .month__weekdays { margin-top: 19px; }
  .weekday {
    justify-self: center; width: 41px; height: 41px; border-radius: 50%;
    background: var(--white); color: var(--ink-purple);
    font-family: "Raleway", sans-serif; font-weight: 700; font-size: 13px;
    display: flex; align-items: center; justify-content: center;
  }
  .month__days { margin-top: 11px; grid-auto-rows: 36.3px; }
  .day { text-align: center; color: var(--white); font-size: 27px; line-height: 36px; font-weight: 400; }
  .day--offset-5 { grid-column-start: 6; }
</style>
</head>
<body>
<main class="calendar-page">
  <section class="hero-photo" role="img" aria-label="Fotografia de uma coruja branca em um campo de flores amarelas"></section>
  <div class="hero-verse">
    <p class="hero-verse__text">Lorem<br>ipsum dolorsit amet<br>czonsectetuer<br>adipiscing elit aenean<br>commodo</p>
    <p class="hero-verse__ref">LOREM IPSUM</p>
  </div>

  <div class="meadow-illustration" role="img" aria-label="Ilustração de uma corujinha sobre capim e flores amarelas"></div>
  <h1 class="year-title">2017</h1>

  <section class="month month--september">
    <h2 class="month__name">Septembro</h2>
    <div class="month__weekdays">
      <span class="weekday">DOM</span><span class="weekday">TER</span><span class="weekday">QUA</span><span class="weekday">QUI</span><span class="weekday">QUI</span><span class="weekday">SEX</span><span class="weekday">SÁB</span>
    </div>
    <div class="month__days">
      <span class="day day--offset-5">1</span><span class="day">2</span>
      <span class="day">3</span><span class="day">4</span><span class="day">5</span><span class="day">6</span><span class="day">7</span><span class="day">8</span><span class="day">9</span>
      <span class="day">10</span><span class="day">11</span><span class="day">12</span><span class="day">13</span><span class="day">14</span><span class="day">15</span><span class="day">16</span>
      <span class="day">17</span><span class="day">18</span><span class="day">19</span><span class="day">20</span><span class="day">21</span><span class="day">22</span><span class="day">23</span>
      <span class="day">24</span><span class="day">25</span><span class="day">26</span><span class="day">27</span><span class="day">28</span><span class="day">29</span><span class="day">30</span>
    </div>
  </section>

  <section class="month month--october">
    <h2 class="month__name">Outubro</h2>
    <div class="month__weekdays">
      <span class="weekday">DOM</span><span class="weekday">TER</span><span class="weekday">QUA</span><span class="weekday">QUI</span><span class="weekday">QUI</span><span class="weekday">SEX</span><span class="weekday">SÁB</span>
    </div>
    <div class="month__days">
      <span class="day">1</span><span class="day">2</span><span class="day">3</span><span class="day">4</span><span class="day">5</span><span class="day">6</span><span class="day">7</span>
      <span class="day">8</span><span class="day">9</span><span class="day">10</span><span class="day">11</span><span class="day">12</span><span class="day">13</span><span class="day">14</span>
      <span class="day">15</span><span class="day">16</span><span class="day">17</span><span class="day">18</span><span class="day">19</span><span class="day">20</span><span class="day">21</span>
      <span class="day">22</span><span class="day">23</span><span class="day">24</span><span class="day">25</span><span class="day">26</span><span class="day">27</span><span class="day">28</span>
      <span class="day">29</span><span class="day">30</span><span class="day">31</span>
    </div>
  </section>
</main>
</body>
</html>
```